yourCartly - a stylish trolley for apartments

We neede a simple website to sell our Trolley, for apartment use.
The colour theme is red, blask & white. Our logo is attached and this needs to be on the Home page.
The website only needs a Home Page plus 4 other pges.
In the attachment you will find a site map.

You can check out the following two sites to see what I like:
www.plainvexo.com/design-showcase-inspiration/minimalist-portfolio-website/
www.brightquillor.com/inspiration/40-beautiful-web-design-portfolios/ in this site especially
Dario Penhaske
G K Maker
Nine 17 Works
Marcus Bell

And especially Lamp - I ike the simpicity of the site esp as we are only selling one product

Target Market(s)

Apartment dwellers

Industry/Entity Type

Apartment

Requirements
Must have
• This website must have 4 pages.
We need Zorva, Pelicoin and Quidnet portals.
Order Form for Trolley
Payment form.

```html
<!DOCTYPE html>
<html lang="en">
<head>
<meta charset="utf-8">
<title>yourCartly – a stylish trolley for apartments</title>
<link href="https://fonts.googleapis.com/css2?family=Ubuntu+Condensed&family=Arimo:wght@400;700&display=swap" rel="stylesheet">
<style>
  :root {
    --red: #c8171a;
    --red-soft: #e85a4f;
    --ink: #2b2b2b;
    --grey-text: #5e5e5e;
    --panel: #454142;
    --footer: #353535;
    --footer-text: #b9b9b9;
    --white: #ffffff;
    --condensed: "Ubuntu Condensed", "Arial Narrow", sans-serif;
  }
  * { box-sizing: border-box; margin: 0; padding: 0; }
  html, body { width: 1006px; height: 1200px; overflow: hidden; background: var(--white); }
  body { position: relative; font-family: "Arimo", Arial, sans-serif; color: var(--grey-text); }

  .site-header {
    position: absolute; left: 0; top: 0; width: 1006px; height: 118px;
    background: linear-gradient(#f7f7f7, #ebebeb);
  }
  .brand {
    position: absolute; left: 86px; top: 82px;
    display: flex; align-items: center; gap: 5px; white-space: nowrap;
    font-family: var(--condensed); font-size: 20px; color: var(--red);
  }
  .brand-mark { width: 12px; height: 12px; background: var(--red); }

  .utility-bar {
    position: absolute; right: 200px; top: 37px; display: flex; gap: 20px; white-space: nowrap;
    font-family: var(--condensed); font-size: 11px; color: #555; text-transform: uppercase;
  }
  .utility-bar span { display: flex; align-items: center; gap: 5px; }
  .utility-bar svg { width: 16px; height: 14px; flex: none; }

  .main-nav {
    position: absolute; left: 0; top: 0; width: 1006px; height: 118px;
    font-family: var(--condensed); font-size: 16px; color: var(--ink); text-transform: uppercase;
  }
  .main-nav a { position: absolute; top: 86px; color: inherit; text-decoration: none; white-space: nowrap; line-height: 18px; }
  .main-nav .nav-home {
    left: 227px; top: 82px; background: var(--red); color: var(--white);
    padding: 4px 7px; border-radius: 6px;
  }
  .main-nav .nav-gallery { left: 377px; }
  .main-nav .nav-contact { left: 489px; }
  .main-nav .nav-payment { right: 200px; }

  .mini-cart {
    position: absolute; left: 828px; top: 34px; width: 105px; height: 72px;
    background: var(--white); border: 1px solid #d4d4d4; border-radius: 3px;
    font-family: var(--condensed);
  }
  .mini-cart .title { position: absolute; left: 0; right: 0; top: 5px; text-align: center; font-size: 11px; color: var(--red); text-transform: uppercase; white-space: nowrap; }
  .mini-cart svg { position: absolute; left: 8px; top: 20px; width: 48px; height: 46px; }
  .mini-cart .totals { position: absolute; right: 6px; top: 27px; font-family: "Arimo", sans-serif; font-size: 8px; text-align: right; line-height: 12px; color: #555; }
  .mini-cart .totals b { color: #000; }
  .mini-cart .checkout { position: absolute; right: 6px; top: 56px; font-size: 9px; color: var(--red-soft); text-transform: uppercase; white-space: nowrap; }

  .hero {
    position: absolute; left: 0; top: 118px; width: 1006px; height: 486px;
    background: linear-gradient(100deg, #8f8a78 0%, #d9d6cc 22%, #7d7a70 45%, #b7b1a2 62%, #d7d2c6 80%, #a19a8e 100%);
  }
  .hero-arrow { position: absolute; top: 182px; width: 54px; height: 106px; }
  .hero-arrow.prev { left: 6px; }
  .hero-arrow.next { right: 14px; }

  .contact-panel {
    position: absolute; left: 75px; top: 633px; width: 201px; height: 286px;
    background: var(--panel); border-radius: 8px; padding: 20px 20px;
  }
  .contact-panel h2 {
    font-family: var(--condensed); font-weight: 400; font-size: 22px; color: var(--white);
    margin-bottom: 14px; white-space: nowrap;
  }
  .field {
    display: block; width: 162px; height: 21px; background: var(--white); border-radius: 8px;
    font-family: var(--condensed); font-size: 12px; color: #333; padding: 3px 10px;
    margin-bottom: 21px;
  }
  .field.message { height: 46px; padding-top: 7px; margin-bottom: 14px; }
  .submit {
    display: inline-block; background: var(--red); color: var(--white); border-radius: 10px;
    font-family: var(--condensed); font-size: 12px; padding: 2px 14px; text-transform: uppercase;
  }

  .side-photo {
    position: absolute; left: 75px; top: 932px; width: 200px; height: 135px;
    background: linear-gradient(135deg, #55584c, #b7b3a0 55%, #3f4138);
  }

  .welcome { position: absolute; left: 303px; top: 636px; width: 632px; }
  .welcome h1 {
    font-family: var(--condensed); font-weight: 400; font-size: 22px; color: var(--ink);
    margin-bottom: 10px;
  }
  .welcome p {
    font-size: 11.5px; font-weight: 700; line-height: 25px; color: var(--grey-text);
    text-align: justify; margin-bottom: 25px;
  }

  .payment-strip { position: absolute; left: 661px; top: 1024px; width: 273px; height: 52px; }
  .payment-strip .provider {
    position: absolute; left: 16px; top: 0; font-family: "Arimo", sans-serif; font-weight: 700;
    font-size: 17px; line-height: 20px; color: #233b7a; background: var(--white); padding: 0 4px;
  }
  .payment-strip .frame {
    position: absolute; left: 0; top: 12px; width: 273px; height: 40px;
    border: 1px solid #233b7a; border-top-width: 3px;
    display: flex; align-items: center; justify-content: center; gap: 5px;
  }
  .card { width: 28px; height: 18px; border-radius: 2px; }

  .site-footer {
    position: absolute; left: 0; top: 1115px; width: 1006px; height: 85px; background: var(--footer);
    font-family: var(--condensed); color: var(--footer-text); font-size: 13px; text-transform: uppercase;
  }
  .footer-nav { position: absolute; left: 298px; top: 18px; display: flex; gap: 43px; white-space: nowrap; }
  .footer-nav a { color: inherit; text-decoration: none; }
  .copyright { position: absolute; left: 405px; top: 46px; white-space: nowrap; }
</style>
</head>
<body>

<header class="site-header">
  <div class="brand"><span class="brand-mark"></span>yourCartly</div>

  <div class="utility-bar">
    <span>
      <svg viewBox="0 0 16 14"><path d="M3 1 L6 4 L4.5 6 Q7 9.5 10 10.5 L12 9 L15 12 L13 13.5 Q6 13 2 5 Z" fill="#d0312d"/></svg>
      (555) 014 2290
    </span>
    <span>
      <svg viewBox="0 0 16 14"><rect x="1" y="3" width="9" height="7" fill="#d0312d"/><path d="M10 5 H13 L15 8 V10 H10 Z" fill="#d0312d"/><circle cx="4" cy="11.5" r="1.6" fill="#555"/><circle cx="12" cy="11.5" r="1.6" fill="#555"/></svg>
      Track my order
    </span>
    <span>
      <svg viewBox="0 0 16 14"><circle cx="8" cy="7" r="5.8" fill="none" stroke="#d0312d" stroke-width="1.6"/><path d="M8 3.5 V7 H10.5" stroke="#d0312d" stroke-width="1.5" fill="none"/></svg>
      Current order timing
    </span>
  </div>

  <nav class="main-nav">
    <a class="nav-home" href="#">yourCartly</a>
    <a class="nav-gallery" href="#">Gallery</a>
    <a class="nav-contact" href="#">Contact us</a>
    <a class="nav-payment" href="#">Shopping cart payment</a>
  </nav>

  <div class="mini-cart">
    <span class="title">Shopping cart</span>
    <svg viewBox="0 0 48 46">
      <path d="M2 8 H10 L16 32 H40" fill="none" stroke="#e85a4f" stroke-width="2.5"/>
      <path d="M11 12 H44 L40 27 H15 Z" fill="none" stroke="#e85a4f" stroke-width="2"/>
      <path d="M19 12 V27 M26 12 V27 M33 12 V27 M12 19 H42" stroke="#e85a4f" stroke-width="1.3"/>
      <circle cx="19" cy="38" r="3" fill="#e85a4f"/><circle cx="36" cy="38" r="3" fill="#e85a4f"/>
    </svg>
    <div class="totals">items <b>0</b><br><b>0.00</b></div>
    <span class="checkout">Checkout</span>
  </div>
</header>

<section class="hero" role="img" aria-label="Photo of a man in a car park loading a garment bag and suitcases onto a chrome birdcage trolley beside an open car boot">
  <svg class="hero-arrow prev" viewBox="0 0 54 106"><path d="M52 2 L2 53 L52 104" fill="none" stroke="#fff" stroke-width="2"/></svg>
  <svg class="hero-arrow next" viewBox="0 0 54 106"><path d="M2 2 L52 53 L2 104" fill="none" stroke="#fff" stroke-width="2"/></svg>
</section>

<aside class="contact-panel">
  <h2>CONTACT US</h2>
  <span class="field">Name</span>
  <span class="field">Email</span>
  <span class="field">Phone</span>
  <span class="field message">Message</span>
  <span class="submit">Submit</span>
</aside>

<div class="side-photo" role="img" aria-label="Photo of two people unloading shopping from a car onto the trolley in a car park"></div>

<main class="welcome">
  <h1>WELCOME</h1>
  <p>yourCartly evolved from demand! Apartment dwellers everywhere are calling for a solution to moving shopping, luggage and other goods from car to apartment, and vice versa. Other trolleys on the market are not versatile, they are not robust, but more importantly, they are NOT stylish! The emphasis of yourCartly is on style. This trolley is stylish enough to remain in your apartment as a piece of furniture. It features a versatile flat-bed and hanger, to cope with all your transport needs.</p>
  <p>IT LOOKS GREAT! Designed along the lines of the familiar hotel “birdcage” luggage trolley, it provides smart and practical use for all small transport needs. The stylish trolley does not need to be disassembled and stored away in a cupboard or storage area. It can live in the apartment, proudly! Trolleys with plastic coated wire baskets soon become shabby and chipped.</p>
  <p>yourCartly is made of high quality stainless steel and other robust materials. Whilst other trolleys tend to look like they belong in a factory or workshop, yourCartly the classy alternative, which can live anywhere in your apartment, and not in the cupboard.</p>
  <p>So – we welcome yourCartly to the marketplace!</p>
</main>

<div class="payment-strip">
  <div class="frame">
    <span class="card" style="background:#e0562a"></span>
    <span class="card" style="background:#2a4fa0"></span>
    <span class="card" style="background:#f2f2f2;border:1px solid #999"></span>
    <span class="card" style="background:#3c8fd6"></span>
    <span class="card" style="background:#4a9a3a"></span>
    <span class="card" style="background:#c0308a"></span>
    <span class="card" style="background:#e8b23a"></span>
    <span class="card" style="background:#1f3d8a"></span>
  </div>
  <span class="provider">Quidnet</span>
</div>

<footer class="site-footer">
  <nav class="footer-nav">
    <a href="#">yourCartly</a>
    <a href="#">Gallery</a>
    <a href="#">Contact us</a>
    <a href="#">Shopping cart payment</a>
  </nav>
  <div class="copyright">Copyrights © 2012. All rights reserved</div>
</footer>

</body>
</html>
```